New LLC consulting company needs a business card design

I need a business card design for new company in Alexandria Virginia called TK Verdane Consulting LLC. The company is focused on consulting for defense and national security issues with expertise in nuclear and space topics. I would like to see designs that are simple and I am open to colors except for brown.

Target Market(s)

All businesses that are seeking consulting help

Industry/Entity Type

Consulting

Contact Information for Business Card

Name of company - TK Verdane Consulting LLC; name (Delia Pratt) President; email: prattdq47@mailvessa.com; Phone: 703-555-0142

Requirements
Must have
• The details described above
Nice to have
• I'm open to all ideas
Should not have
• No brown

```html
<!DOCTYPE html>
<html lang="en">
<head>
<meta charset="utf-8">
<title>Delia Pratt – TK Verdane Consulting LLC</title>
<link href="https://fonts.googleapis.com/css2?family=Montserrat:wght@400;500;700&display=swap" rel="stylesheet">
<style>
  :root {
    --backdrop: #9a9a9a;
    --card: #ffffff;
    --accent: #1f3a68;
    --ink: #2b2b2b;
  }
  * { margin: 0; padding: 0; box-sizing: border-box; }
  html, body {
    width: 1200px;
    height: 1059px;
    overflow: hidden;
    background: var(--backdrop);
  }
  .business-card {
    position: absolute;
    left: 50px;
    top: 215px;
    width: 1100px;
    height: 629px;
    background: var(--card);
    border-radius: 40px;
    font-family: "Montserrat", Arial, sans-serif;
    color: var(--ink);
  }
  .holder-name {
    position: absolute;
    left: 62px;
    top: 58px;
    font-size: 50px;
    font-weight: 700;
    letter-spacing: -0.5px;
    color: var(--accent);
    line-height: 1.1;
  }
  .holder-title {
    position: absolute;
    left: 62px;
    top: 127px;
    font-size: 27px;
    font-weight: 400;
    line-height: 1.2;
  }
  .company {
    position: absolute;
    right: 63px;
    top: 270px;
    display: flex;
    align-items: center;
    gap: 16px;
  }
  .company-mark {
    width: 22px;
    height: 22px;
    border-radius: 50%;
    background: var(--accent);
    flex: none;
  }
  .company-name {
    font-size: 34px;
    font-weight: 700;
    color: var(--accent);
    line-height: 1.2;
    white-space: nowrap;
  }
  .contact-row {
    position: absolute;
    left: 62px;
    right: 63px;
    top: 526px;
    display: flex;
    justify-content: space-between;
    align-items: center;
    font-size: 28px;
    font-weight: 400;
  }
  .contact-item {
    display: flex;
    align-items: center;
    gap: 12px;
    white-space: nowrap;
  }
  .contact-icon { fill: var(--accent); flex: none; }
</style>
</head>
<body>
  <div class="business-card">
    <h1 class="holder-name">Delia Pratt</h1>
    <p class="holder-title">President</p>

    <div class="company">
      <span class="company-mark" aria-hidden="true"></span>
      <span class="company-name">TK Verdane Consulting LLC</span>
    </div>

    <div class="contact-row">
      <div class="contact-item email">
        <svg class="contact-icon" width="24" height="18" viewBox="0 0 24 18" aria-hidden="true">
          <path d="M0 0h24v2L12 10 0 2z"/>
          <path d="M0 4l8 5.5L0 16zM24 4l-8 5.5 8 6.5zM9.5 10.5L12 12.2l2.5-1.7L24 18H0z"/>
        </svg>
        <span>prattdq47@mailvessa.com</span>
      </div>
      <div class="contact-item phone">
        <svg class="contact-icon" width="28" height="28" viewBox="0 0 24 24" aria-hidden="true">
          <path d="M6.6 10.8c1.4 2.8 3.8 5.1 6.6 6.6l2.2-2.2c.3-.3.7-.4 1-.2 1.1.4 2.3.6 3.6.6.6 0 1 .4 1 1V20c0 .6-.4 1-1 1C10.6 21 3 13.4 3 4c0-.6.4-1 1-1h3.5c.6 0 1 .4 1 1 0 1.3.2 2.5.6 3.6.1.3 0 .7-.2 1z"/>
          <path d="M14 2.5a7.5 7.5 0 0 1 7.5 7.5h-1.8A5.7 5.7 0 0 0 14 4.3zM14 6a4 4 0 0 1 4 4h-1.8A2.2 2.2 0 0 0 14 7.8z"/>
        </svg>
        <span>703-555-0142</span>
      </div>
    </div>
  </div>
</body>
</html>
```